Zelvo Stationary

Design the stationary of Zelvo Promotions Group.

Zelvo is a BTL company, BTL meaning "below the line". In other words Zelvo is a Promotional Marketing company (the company that design the brands promotional activities).

The design should transmit creativity, agility, boldness.

I need:
* Bis Card
* Letter head
* Envelopes, both vertical and horizontal (for legal size), and letter envelope
* Folders
* PPT template (Title page and regular page)
* CD slip (CD envelope)
* ID card (employee card)

And what ever else you want to throw in.
Updates

Guys,

Something I missed from the brief.   The predominat color should be RED.

Also, have fun and play with the exclamation mark (!) of the logo. 

Hi guys, more comments:

Remember that Zelvo is a "creativity" agency, not in the advertising side but on the promotional side, and that should reflect on the stationary.

 I want a bold design.  Bold and yet crisp.

 

Guys, i just uploaded the Logo in AI format.

I Also uploaded the actual Zelvo Bis Card, wich I like.  So I will like to see some designs with that bis card approach.

Guys, I am so sorry, but I notice in your last post that I upladed a wrong design ("13154_promotions_group_zelvo_brief225630.ai").  The problem was that I asked the designer the file in AI format and he send me thw wrong file, and since I dont have Illustrator I could not verify it.

The differences are minor, I just already ask him the correct one (similar to the EPS file).

Sorry                                   

Just post the correct AI file : "Zelvo Logo.ai"

Reason: I'm expecting more designs to choose from and also I wont be available tomorrow to decide.

Reason: Sorry guys, but we are not there yet!

Target Market(s)

Marketing directors, Marketing Managers

Industry/Entity Type

Legal

Requirements
Must have
• Must work with the logo attached.
The predominat color should be RED.
Play and have fun with the exclamation mark (!).
Should not have
• * No old fonts

Should not be:
* boring
* Informal
* rigid

```html
<!DOCTYPE html>
<html lang="es">
<head>
<meta charset="utf-8">
<title>Zelvo Promotions Group — Letterhead</title>
<link rel="stylesheet" href="https://fonts.googleapis.com/css2?family=Poppins:wght@600;700&display=swap">
<style>
  :root {
    --paper: #ffffff;
    --ink: #111111;
    --brand-red: #c8141e;
    --band-deep: #5e070b;
    --band-mid: #8c0f16;
    --band-light: #a8161f;
    --band-text: #ffffff;
  }
  * { margin: 0; padding: 0; box-sizing: border-box; }
  html, body {
    width: 848px;
    height: 1200px;
    overflow: hidden;
    background: var(--paper);
  }
  .letterhead {
    position: relative;
    width: 848px;
    height: 1200px;
    background: var(--paper);
    font-family: "Poppins", "Century Gothic", sans-serif;
  }
  .brand-mark {
    position: absolute;
    display: flex;
    align-items: center;
    gap: 10px;
    font-weight: 700;
    white-space: nowrap;
  }
  .brand-mark--header {
    top: 52px;
    left: 30px;
    color: var(--ink);
    font-size: 26px;
    letter-spacing: -0.2px;
  }
  .brand-mark__dot {
    width: 22px;
    height: 22px;
    border-radius: 50%;
    background: var(--brand-red);
    flex: none;
  }
  .footer-band {
    position: absolute;
    left: 0;
    bottom: 0;
    width: 848px;
    height: 111px;
    background:
      radial-gradient(ellipse 360px 140px at 440px 55px, var(--band-light) 0%, var(--band-mid) 55%, transparent 100%),
      linear-gradient(90deg, var(--band-deep) 0%, var(--band-mid) 45%, var(--band-mid) 60%, var(--band-deep) 100%);
    color: var(--band-text);
  }
  .contact {
    position: absolute;
    left: 31px;
    top: 21px;
    font-size: 11.5px;
    font-weight: 600;
    line-height: 13.6px;
  }
  .contact__web {
    margin-top: 3px;
    font-size: 19px;
    line-height: 22px;
    font-weight: 600;
    letter-spacing: 0.2px;
  }
  .brand-mark--footer {
    right: 28px;
    top: 40px;
    color: var(--band-text);
    font-size: 22px;
  }
  .brand-mark--footer .brand-mark__dot {
    background: var(--band-text);
    width: 18px;
    height: 18px;
  }
</style>
</head>
<body>
  <main class="letterhead">
    <header class="brand-mark brand-mark--header">
      <span>Zelvo Promotions Group</span>
      <span class="brand-mark__dot"></span>
    </header>

    <footer class="footer-band">
      <address class="contact" style="font-style: normal;">
        <p>Calle 12 No. 48 Ens Los Pinos Santo Domingo,</p>
        <p>Republica Dominicana</p>
        <p>Tell: 809.555.0147</p>
        <p>Fax: 809.555.0192</p>
        <p class="contact__web">www.zelvo.com.do</p>
      </address>
      <div class="brand-mark brand-mark--footer">
        <span>Zelvo Promotions Group</span>
        <span class="brand-mark__dot"></span>
      </div>
    </footer>
  </main>
</body>
</html>
```